Animal Eye Clinic needs a Business card

We are a new veterinary ophthalmology practice (Ridgeline Pet Vision Care) and we need a business card designed. We only see animal eyes - we are not a regular veterinary clinic. We already have a logo. We are looking for a professional, good looking business card to hand out to our clients. We are looking for something simple but professional and contemporary. Our logo is likely the only picture/graphic that needs to be on the card.
Updates

Contact Information for Business Card

Delia Vossman, BSc, DVM, MSc, DipACVO
Veterinary Ophthalmologist

Phone: 250.418.3927
Email: ridgelinepetvisioncare@mailbox-example.net
Website: ridgelinepetvisioncare-example.net
Address: 1874 Thornbury Rd
Kelowna, BC, V1X 4M9

Colors

Designer to choose colors to be used in the design.

Requirements
Must have
• Our logo (attached)

```html
<!DOCTYPE html>
<html lang="en">
<head>
<meta charset="utf-8">
<title>Ridgeline Pet Vision Care – Business Card</title>
<link rel="stylesheet" href="https://fonts.googleapis.com/css2?family=Roboto:wght@300;400;500&display=swap">
<style>
  :root {
    --teal: #0f98ab;
    --teal-deep: #0b8a9c;
    --ink: #5f6468;
    --grey-band: #8c8f92;
    --paper: #ffffff;
    --backdrop: #2a2a2a;
    --faint: #eef6f8;
  }
  * { box-sizing: border-box; margin: 0; padding: 0; }
  html, body { width: 1200px; height: 930px; overflow: hidden; }
  body {
    background: var(--backdrop);
    font-family: "Roboto", Arial, sans-serif;
    position: relative;
  }
  .card {
    position: absolute;
    width: 600px;
    height: 343px;
    border-radius: 22px;
    overflow: hidden;
    box-shadow: 0 14px 30px rgba(0,0,0,.45);
  }
  /* Front */
  .card-front {
    left: 60px; top: 70px;
    background: linear-gradient(135deg, #20a9bb 0%, var(--teal) 50%, var(--teal-deep) 100%);
  }
  .brand {
    position: absolute;
    display: flex;
    align-items: center;
    gap: 14px;
    font-weight: 500;
    letter-spacing: .5px;
    white-space: nowrap;
  }
  .brand-dot {
    border-radius: 50%;
    flex: none;
  }
  .card-front .brand {
    left: 110px; top: 150px;
    color: var(--paper);
    font-size: 28px;
  }
  .card-front .brand-dot { width: 44px; height: 44px; background: var(--paper); }

  /* Back */
  .card-back {
    left: 540px; top: 510px;
    background: var(--paper);
  }
  .back-decor {
    position: absolute;
    right: 40px; top: 30px;
    width: 270px; height: 270px;
    border-radius: 50%;
    background: var(--faint);
  }
  .card-back .brand {
    left: 300px; top: 90px;
    color: var(--teal);
    font-size: 17px;
  }
  .card-back .brand-dot { width: 30px; height: 30px; background: var(--teal); }
  .person { position: absolute; left: 36px; top: 34px; }
  .person-name { color: var(--teal); font-size: 34px; font-weight: 400; line-height: 1.1; }
  .person-role { color: var(--ink); font-size: 14px; font-weight: 300; line-height: 1.35; margin-top: 4px; }
  .rule {
    position: absolute; left: 36px;
    width: 40px; height: 2px; background: var(--teal);
  }
  .rule-1 { top: 140px; }
  .rule-2 { top: 216px; }
  .address {
    position: absolute; left: 36px; top: 158px;
    color: var(--ink); font-size: 15px; font-weight: 300; line-height: 1.4;
  }
  .contacts { position: absolute; left: 36px; top: 232px; list-style: none; }
  .contacts li {
    display: flex; align-items: center; gap: 10px;
    color: var(--ink); font-size: 14px; font-weight: 300; line-height: 22px;
  }
  .contacts svg { width: 12px; height: 12px; flex: none; }
  .contacts .web strong { font-weight: 500; }
  .band-teal {
    position: absolute; left: 0; bottom: 0;
    width: 62%; height: 12px; background: var(--teal);
  }
  .band-grey {
    position: absolute; right: 0; bottom: 0;
    width: 38%; height: 20px; background: var(--grey-band);
  }
</style>
</head>
<body>

<section class="card card-front" aria-label="Business card front">
  <div class="brand"><span class="brand-dot"></span>Ridgeline Pet Vision Care</div>
</section>

<section class="card card-back" aria-label="Business card back">
  <div class="back-decor"></div>
  <div class="brand"><span class="brand-dot"></span>Ridgeline Pet Vision Care</div>

  <div class="person">
    <h1 class="person-name">Delia Vossman</h1>
    <p class="person-role">BSc, DVM, MSc, DipACVO<br>Veterinary Ophthalmologist</p>
  </div>

  <div class="rule rule-1"></div>
  <p class="address">Address: 1874 Thornbury Rd<br>Kelowna, BC, V1X 4M9</p>
  <div class="rule rule-2"></div>

  <ul class="contacts">
    <li>
      <svg viewBox="0 0 12 12" aria-hidden="true"><path d="M2.5 1 L4.5 1 L5.2 3.6 L4 4.6 C4.6 6 5.9 7.4 7.4 8 L8.4 6.8 L11 7.5 L11 9.5 C11 10.3 10.3 11 9.5 11 C5 11 1 7 1 2.5 C1 1.7 1.7 1 2.5 1 Z" fill="var(--teal)"/></svg>
      250.418.3927
    </li>
    <li>
      <svg viewBox="0 0 12 12" aria-hidden="true"><rect x="1" y="2.5" width="10" height="7" fill="none" stroke="var(--teal)" stroke-width="1.2"/><path d="M1 2.5 L6 6.5 L11 2.5" fill="none" stroke="var(--teal)" stroke-width="1.2"/></svg>
      ridgelinepetvisioncare@mailbox-example.net
    </li>
    <li class="web">
      <svg viewBox="0 0 12 12" aria-hidden="true"><circle cx="6" cy="6" r="5" fill="none" stroke="var(--teal)" stroke-width="1.2"/><path d="M1 6 H11 M6 1 C3.5 3.5 3.5 8.5 6 11 M6 1 C8.5 3.5 8.5 8.5 6 11" fill="none" stroke="var(--teal)" stroke-width="1"/></svg>
      <span>www.<strong>ridgelinepetvisioncare-example</strong>.net</span>
    </li>
  </ul>

  <div class="band-teal"></div>
  <div class="band-grey"></div>
</section>

</body>
</html>
```